business card deign

Logo needs the following on it.
1. attached logo
2. Tagline - "If it keeps a drink cold or the party going...we do it!"
3. Name- Dalton Pikes, Founder and CPO
4. Address - 412 E. Carver Avenue, Ste 2207, Tampa, FL. 33917
5. Phone - 555.318.4726

```html
<!DOCTYPE html>
<html lang="en">
<head>
<meta charset="utf-8">
<title>Boundly Business Card</title>
<link rel="stylesheet" href="https://fonts.googleapis.com/css2?family=Roboto:wght@400;700&display=swap">
<style>
  :root {
    --page-bg: #e6e4e1;
    --card-bg: #141414;
    --card-edge: #2a2a2a;
    --ink-white: #ffffff;
    --ink-soft: #e8e8e8;
    --deco-top: #4a4a4a;
    --deco-bottom: #1c1c1c;
  }
  * { margin: 0; padding: 0; box-sizing: border-box; }
  html, body { width: 1200px; height: 711px; overflow: hidden; }
  body {
    background: var(--page-bg);
    font-family: "Roboto", Arial, sans-serif;
    position: relative;
  }
  .card {
    position: absolute;
    top: 195px;
    width: 540px;
    height: 320px;
    border-radius: 24px;
    background: var(--card-bg);
    border: 1px solid var(--card-edge);
    overflow: hidden;
  }
  .card--back { left: 35px; }
  .card--front { left: 625px; }

  .deco-figure {
    position: absolute;
    border-radius: 48% 40% 10% 60% / 40% 45% 10% 60%;
    background: linear-gradient(180deg, var(--deco-top), var(--deco-bottom) 70%);
    opacity: 0.85;
  }
  .card--back .deco-figure { left: 215px; top: 30px; width: 240px; height: 290px; }
  .card--front .deco-figure { left: 375px; top: 110px; width: 150px; height: 210px; }

  .wordmark {
    font-weight: 700;
    color: var(--ink-white);
    letter-spacing: 0.45em;
    text-transform: uppercase;
  }
  .card--back .wordmark {
    position: absolute;
    right: 22px;
    bottom: 26px;
    font-size: 22px;
  }

  .identity {
    position: absolute;
    top: 26px;
    right: 44px;
    text-align: right;
    color: var(--ink-white);
  }
  .identity__name { font-size: 24px; font-weight: 700; }
  .identity__title { font-size: 14px; margin-top: 3px; color: var(--ink-soft); }
  .identity-bar {
    position: absolute;
    top: 24px;
    right: 0;
    width: 26px;
    height: 56px;
    background: var(--ink-white);
  }

  .brand {
    position: absolute;
    left: 36px;
    top: 104px;
    display: flex;
    align-items: center;
    gap: 12px;
  }
  .brand__square { width: 18px; height: 18px; background: var(--ink-white); }
  .brand .wordmark { font-size: 26px; }

  .tagline {
    position: absolute;
    left: 36px;
    top: 172px;
    width: 240px;
    font-size: 13px;
    line-height: 1.45;
    color: var(--ink-soft);
  }
  .contact {
    position: absolute;
    left: 36px;
    top: 230px;
    list-style: none;
    font-size: 13px;
    line-height: 1.45;
    color: var(--ink-soft);
  }
  .contact__item { display: flex; align-items: flex-start; gap: 9px; margin-bottom: 3px; }
  .contact__icon { width: 13px; height: 13px; margin-top: 3px; flex: none; }
</style>
</head>
<body>
  <section class="card card--back">
    <div class="deco-figure" role="img" aria-label="Large faint brand mascot silhouette"></div>
    <div class="wordmark">Boundly</div>
  </section>

  <section class="card card--front">
    <div class="deco-figure" role="img" aria-label="Faint brand mascot silhouette"></div>
    <div class="identity-bar"></div>
    <div class="identity">
      <div class="identity__name">Dalton Pikes</div>
      <div class="identity__title">Founder and CPO</div>
    </div>
    <div class="brand">
      <span class="brand__square"></span>
      <span class="wordmark">Boundly</span>
    </div>
    <p class="tagline">If it keeps a drink cold or the party going...we do it!</p>
    <ul class="contact">
      <li class="contact__item">
        <svg class="contact__icon" viewBox="0 0 24 24" fill="#fff"><path d="M6.6 10.8a15.1 15.1 0 0 0 6.6 6.6l2.2-2.2c.3-.3.7-.4 1-.2 1.1.4 2.3.6 3.6.6.6 0 1 .4 1 1V20c0 .6-.4 1-1 1A17 17 0 0 1 3 4c0-.6.4-1 1-1h3.5c.6 0 1 .4 1 1 0 1.3.2 2.5.6 3.6.1.3 0 .7-.2 1z"/></svg>
        <span>555.318.4726</span>
      </li>
      <li class="contact__item">
        <svg class="contact__icon" viewBox="0 0 24 24" fill="#fff"><path d="M12 2a7 7 0 0 0-7 7c0 5.2 7 13 7 13s7-7.8 7-13a7 7 0 0 0-7-7zm0 9.5A2.5 2.5 0 1 1 12 6.5a2.5 2.5 0 0 1 0 5z"/></svg>
        <span>412 E. Carver Avenue,<br>Ste 2207, Tampa, FL. 33917</span>
      </li>
    </ul>
  </section>
</body>
</html>
```